New Business Card Design Project

Need a design that will create an impact / strong impression towards our clients for our business. We are in the lighting business and we do lighting retrofits for large commercial to industrial clientele.

Target Market(s)

Lighting Industry

Industry/Entity Type

Business

Font styles to use
Other font styles liked:
• we would like to use the font on our logo, not sure what it is though..

Requirements
Must have
• Our logo.
Nice to have
• We are open to suggestions that have to do with lighting.

```html
<!DOCTYPE html>
<html lang="en">
<head>
<meta charset="utf-8">
<title>Brightwell Retrofit Co. – Business Card</title>
<link href="https://fonts.googleapis.com/css2?family=Montserrat:wght@400;500;600&display=swap" rel="stylesheet">
<style>
  :root {
    --backdrop: #d3d3d3;
    --card: #ffffff;
    --green-deep: #1f4d25;
    --green: #178a3c;
    --green-light: #6cc04a;
    --grey-text: #6b6b6b;
  }
  * { box-sizing: border-box; margin: 0; padding: 0; }
  html, body { width: 1200px; height: 800px; overflow: hidden; }
  body {
    background: var(--backdrop);
    font-family: "Montserrat", sans-serif;
    display: flex;
    align-items: center;
    justify-content: center;
    gap: 50px;
  }
  .card {
    width: 525px;
    height: 300px;
    background: var(--card);
    position: relative;
    box-shadow: 0 4px 14px rgba(0,0,0,0.18);
  }
  .brand {
    display: flex;
    align-items: center;
    gap: 10px;
    color: var(--green);
    font-weight: 600;
    white-space: nowrap;
  }
  .brand-mark {
    width: 14px;
    height: 14px;
    background: var(--green-light);
  }
  .brand-rule {
    height: 1px;
    background: var(--green);
  }

  /* front */
  .card-front .brand-block {
    position: absolute;
    left: 50%;
    top: 108px;
    transform: translateX(-50%);
    width: 380px;
  }
  .card-front .brand { font-size: 30px; justify-content: center; }
  .card-front .brand-mark { width: 20px; height: 20px; }
  .card-front .brand-rule { margin-top: 10px; }
  .card-front .website {
    position: absolute;
    right: 34px;
    bottom: 30px;
    font-size: 13px;
    color: var(--grey-text);
    letter-spacing: 0.5px;
  }
  .card-front .website span { color: var(--green); }

  /* back */
  .card-back .brand-block {
    position: absolute;
    left: 50%;
    top: 46px;
    transform: translateX(-50%);
    width: 300px;
  }
  .card-back .brand { font-size: 21px; justify-content: center; }
  .card-back .brand-rule { margin-top: 8px; }
  .details {
    position: absolute;
    top: 128px;
    left: 0;
    right: 0;
    display: flex;
    justify-content: center;
    align-items: center;
    gap: 20px;
  }
  .person { text-align: right; }
  .person-name {
    font-size: 18px;
    font-weight: 500;
    color: var(--green);
    letter-spacing: 0.5px;
    text-transform: uppercase;
  }
  .person-role {
    font-size: 14px;
    color: var(--grey-text);
    margin-top: 2px;
  }
  .divider {
    width: 1.5px;
    height: 70px;
    background: var(--green-light);
  }
  .contact-list { list-style: none; }
  .contact-list li {
    display: flex;
    align-items: center;
    gap: 8px;
    font-size: 12.5px;
    color: var(--grey-text);
    line-height: 22px;
  }
  .contact-list svg { width: 11px; height: 11px; fill: var(--green-deep); flex: none; }
  .address {
    position: absolute;
    left: 0;
    right: 0;
    bottom: 40px;
    text-align: center;
    font-size: 13px;
    color: var(--grey-text);
    letter-spacing: 0.4px;
  }
</style>
</head>
<body>

<section class="card card-front">
  <div class="brand-block">
    <div class="brand"><span class="brand-mark"></span>Brightwell Retrofit Co.</div>
    <div class="brand-rule"></div>
  </div>
  <p class="website">www.<span>brightwellretrofit</span>.com</p>
</section>

<section class="card card-back">
  <div class="brand-block">
    <div class="brand"><span class="brand-mark"></span>Brightwell Retrofit Co.</div>
    <div class="brand-rule"></div>
  </div>

  <div class="details">
    <div class="person">
      <p class="person-name">Daniel Harper</p>
      <p class="person-role">Founder</p>
    </div>
    <div class="divider"></div>
    <ul class="contact-list">
      <li>
        <svg viewBox="0 0 24 24" aria-hidden="true"><path d="M6.6 10.8a15.1 15.1 0 0 0 6.6 6.6l2.2-2.2c.3-.3.7-.4 1-.2 1.1.4 2.3.6 3.6.6.6 0 1 .4 1 1V20c0 .6-.4 1-1 1A17 17 0 0 1 3 4c0-.6.4-1 1-1h3.5c.6 0 1 .4 1 1 0 1.3.2 2.5.6 3.6.1.3 0 .7-.2 1z"/></svg>
        0400 555 019
      </li>
      <li>
        <svg viewBox="0 0 24 24" aria-hidden="true"><path d="M2 5h20v14H2z M2 5l10 8 10-8" fill="none" stroke="#1f4d25" stroke-width="2.4"/></svg>
        hello@brightwellretrofit.com
      </li>
      <li>
        <svg viewBox="0 0 24 24" aria-hidden="true"><circle cx="12" cy="12" r="10" fill="none" stroke="#1f4d25" stroke-width="2.2"/><path d="M2 12h20M12 2c3 3 3 17 0 20M12 2c-3 3-3 17 0 20" fill="none" stroke="#1f4d25" stroke-width="1.8"/></svg>
        www.brightwellretrofit.com
      </li>
    </ul>
  </div>

  <p class="address">4870 Alder Ridge Road, Suite 12 Fairview AZ 85000</p>
</section>

</body>
</html>
```